Fitness Equipment Repair Business Needs a Catchy New Business Card

We have an existing business card, however, it is quite plain and boring. We are expanding primarily in the commercial area (gyms, studios, apartment complexes etc). The business card will serve as eye candy to those managers/owners that can't be met for a face to face.
Originally I was planning for a brochure as well, but all of our information is better summarized on our website. (brightloopservice.ca).
I would like the card to match the colour scheme of the website and utilize the logo. It should have a professional clean feel to it, however, a little colouring outside the lines wouldn't hurt.
The example card is for my service technician (Colin Marsh). If possible I would like to be able to edit the text to use for more than one person.

Industry/Entity Type

Appliance Repair

Contact Information for Business Card

Clean, crisp and professional but needs to be eye catching. Preferably using the black, white and red colour scheme matching the website. Double sided would be nice, but is not necessary.

Colors
ec1f27
ffffff
000000

Requirements
Must have
• Must be able to edit name, phone number and title to use for multiple people. Must show the company website (brightloopservice.ca).

```html
<!DOCTYPE html>
<html lang="en">
<head>
<meta charset="utf-8">
<title>Brightloop Service – Business Card</title>
<link href="https://fonts.googleapis.com/css2?family=Marcellus+SC&family=PT+Sans:wght@400&display=swap" rel="stylesheet">
<style>
  :root {
    --red: #ec1f27;
    --red-deep: #c9141b;
    --black: #000000;
    --white: #ffffff;
    --grey-text: #d8d8d8;
    --backdrop: #e9e6e2;
  }
  * { box-sizing: border-box; margin: 0; padding: 0; }
  html, body {
    width: 1200px; height: 987px; overflow: hidden;
    background: var(--backdrop);
  }
  .sheet { position: relative; width: 1200px; height: 987px; }

  .card {
    position: absolute; left: 200px; width: 800px;
    box-shadow: 0 4px 14px rgba(0,0,0,.25);
    overflow: hidden;
  }

  /* Front */
  .card-front { top: 40px; height: 444px; background: var(--black); }
  .card-front .accent-rule {
    position: absolute; left: 0; right: 0; bottom: 10px; height: 3px; background: var(--white);
  }
  .card-front .accent-band {
    position: absolute; left: 0; right: 0; bottom: 0; height: 10px; background: var(--red);
  }
  .brand {
    position: absolute; left: 70px; top: 200px;
    display: flex; align-items: center; gap: 18px;
  }
  .brand-dot { width: 34px; height: 34px; border-radius: 50%; background: var(--red); }
  .brand-name {
    font-family: "Marcellus SC", serif; color: var(--white); font-size: 26px; letter-spacing: .5px;
  }
  .contact { position: absolute; left: 460px; top: 104px; color: var(--white); font-family: "PT Sans", sans-serif; }
  .person-name {
    font-family: "Marcellus SC", serif; color: var(--red); font-size: 31px; letter-spacing: 1.5px; line-height: 1;
  }
  .person-title {
    font-family: "Marcellus SC", serif; color: var(--grey-text); font-size: 21px; letter-spacing: 1px; margin-top: 6px;
  }
  .address { font-size: 19px; line-height: 29px; margin-top: 24px; }
  .lines { list-style: none; margin-top: 18px; font-size: 19px; line-height: 30px; }
  .lines li { display: flex; align-items: center; gap: 10px; }
  .lines svg { width: 16px; height: 16px; fill: var(--red); flex: none; }
  .lines .note { font-size: 15px; }

  /* Back */
  .card-back { top: 508px; height: 444px; background: var(--red); }
  .mascot-area {
    position: absolute; left: 440px; top: 12px; width: 360px; height: 432px;
    background: linear-gradient(160deg, var(--red) 0%, var(--red-deep) 100%);
    border-radius: 160px 160px 0 0;
  }
  .back-name {
    position: absolute; left: 48px; top: 362px;
    font-family: "Marcellus SC", serif; color: var(--white); font-size: 29px; letter-spacing: 1px;
  }
  .back-web {
    position: absolute; left: 48px; top: 402px;
    font-family: "PT Sans", sans-serif; color: var(--white); font-size: 19px; letter-spacing: 3.5px;
  }
</style>
</head>
<body>
<main class="sheet">
  <section class="card card-front">
    <div class="brand">
      <span class="brand-dot"></span>
      <span class="brand-name">Brightloop Service</span>
    </div>
    <div class="contact">
      <h1 class="person-name">Colin Marsh</h1>
      <p class="person-title">Service technician</p>
      <p class="address">1875 Ridgeview Cres NW<br>Edmonton AB T5K 2P9</p>
      <ul class="lines">
        <li><svg viewBox="0 0 24 24"><path d="M6.6 10.8a15.1 15.1 0 0 0 6.6 6.6l2.2-2.2a1 1 0 0 1 1-.25 11.4 11.4 0 0 0 3.6.57 1 1 0 0 1 1 1V20a1 1 0 0 1-1 1A17 17 0 0 1 3 4a1 1 0 0 1 1-1h3.5a1 1 0 0 1 1 1c0 1.25.2 2.45.57 3.57a1 1 0 0 1-.25 1z"/></svg><span>587-555-0142<span class="note">(Personal)</span></span></li>
        <li><svg viewBox="0 0 24 24"><path d="M6.6 10.8a15.1 15.1 0 0 0 6.6 6.6l2.2-2.2a1 1 0 0 1 1-.25 11.4 11.4 0 0 0 3.6.57 1 1 0 0 1 1 1V20a1 1 0 0 1-1 1A17 17 0 0 1 3 4a1 1 0 0 1 1-1h3.5a1 1 0 0 1 1 1c0 1.25.2 2.45.57 3.57a1 1 0 0 1-.25 1z"/></svg><span>780-555-0187<span class="note">(Service Line)</span></span></li>
        <li><svg viewBox="0 0 24 24"><path d="M2 5h20v14H2z M3.5 6.5 12 13l8.5-6.5" /></svg><span>hello@brightloopservice.ca</span></li>
      </ul>
    </div>
    <div class="accent-rule"></div>
    <div class="accent-band"></div>
  </section>

  <section class="card card-back">
    <div class="mascot-area" role="img" aria-label="Line illustration of a muscular technician in a hard hat holding a wrench"></div>
    <p class="back-name">Brightloop Service</p>
    <p class="back-web">www.brightloopservice.ca</p>
  </section>
</main>
</body>
</html>
```